Very visible CoWorking Building Sign overlooking downtown LA and 110 freeway

Our building is drab but very visible and in the best location. We need a great sign for our monolith that overlooks downtown LA and the 100 freeway. We are a new CoWorking business and would like to have a few things we do on the sign: private offices, virtual offices, CoWorking Lounge. Everything we have seen is ho-hum. Can you get us noticed? We need people to know what we do and that we are here but in a creative, professional, unique sign.
Target Market(s)
People who have a business in DTLA, remote workers and those who work from home who need a professional address.
Requirements
Must have
- Our logo (which can be somewhat reimagined) which has our address 2417 on it. The three things we focus on: Private Offices, Virtual Offices, CoWorking Lounge. Incorporate some Navy. Readable from several hundred feet away.
Nice to have
- Mural feel? Something inspirational in this crazy COVID times? Graphics? Color block. I like the idea of decorative but it has to be readable as a building sign. The same with the use of colors. Our colors are grays and navy but with a pop of the chartreuse (we have 2 velvet chartreuse chairs in the space). Helpful to view our website: Harborview2417.com.
Should not have
- Not too graffiti. Keep it professional but unique and wow.

```html
<!DOCTYPE html>
<html lang="en">
<head>
<meta charset="utf-8">
<title>2417 Harborview – Building Sign</title>
<link rel="stylesheet" href="https://fonts.googleapis.com/css2?family=Libre+Caslon+Text:wght@700&display=swap">
<style>
  :root {
    --navy: #13284c;
    --chartreuse: #80c342;
    --chartreuse-soft: #c9e6a6;
    --white: #ffffff;
    --backdrop: #d9d9d9;
  }
  * { margin: 0; padding: 0; box-sizing: border-box; }
  html, body { width: 834px; height: 1200px; overflow: hidden; background: var(--backdrop); }
  .canvas { position: relative; width: 834px; height: 1200px; }
  .sign {
    position: absolute; left: 0; top: 288px;
    width: 834px; height: 625px;
    background: var(--white);
    overflow: hidden;
  }
  .sign-frame { position: absolute; inset: 0; }
  .vine-ornament {
    position: absolute; left: 150px; top: 8px; width: 535px; height: 115px;
    background: radial-gradient(ellipse at center, var(--chartreuse-soft) 0%, rgba(201,230,166,0.5) 55%, rgba(255,255,255,0) 75%);
  }
  .service {
    position: absolute; top: 167px; width: 220px;
    text-align: center;
  }
  .service-icon { display: block; width: 192px; height: 192px; margin: 0 auto; }
  .service-label {
    margin-top: 22px;
    font-family: "Libre Caslon Text", Georgia, serif;
    font-weight: 700; font-size: 26px; line-height: 31px;
    color: var(--navy); text-transform: uppercase; letter-spacing: 0.5px;
  }
  .service--private { left: 55px; }
  .service--virtual { left: 298px; }
  .service--lounge { left: 536px; }
  .divider { position: absolute; top: 183px; width: 2px; height: 190px; background: var(--navy); }
  .divider--one { left: 289px; }
  .divider--two { left: 528px; }
  .brand-name {
    position: absolute; left: 0; right: 0; top: 515px;
    text-align: center;
    font-family: "Libre Caslon Text", Georgia, serif;
    font-weight: 700; font-size: 46px; letter-spacing: 2px;
    color: var(--navy);
  }
</style>
</head>
<body>
<main class="canvas">
  <section class="sign">
    <svg class="sign-frame" viewBox="0 0 834 625" width="834" height="625" aria-hidden="true">
      <g fill="none" stroke="var(--chartreuse)" stroke-width="2.5">
        <!-- outer frame lines -->
        <path d="M10 10 H140 M694 10 H824 M10 10 V160 M824 10 V160"/>
        <path d="M10 615 H240 M594 615 H824 M10 615 V395 M824 615 V395"/>
        <!-- inner frame lines -->
        <path d="M30 30 V230 M804 30 V230 M30 595 V395 M804 595 V395"/>
      </g>
      <g fill="var(--chartreuse)">
        <path d="M28 28 H66 V36 H36 V66 H28 Z"/>
        <path d="M806 28 H768 V36 H798 V66 H806 Z"/>
        <path d="M28 597 H66 V589 H36 V559 H28 Z"/>
        <path d="M806 597 H768 V589 H798 V559 H806 Z"/>
      </g>
    </svg>

    <div class="vine-ornament" role="img" aria-label="Chartreuse vine flourish ornament"></div>

    <div class="service service--private">
      <svg class="service-icon" viewBox="0 0 192 192" aria-hidden="true">
        <circle cx="96" cy="96" r="96" fill="var(--navy)"/>
        <g fill="none" stroke="var(--white)" stroke-width="4" stroke-linejoin="round" stroke-linecap="round">
          <rect x="32" y="38" width="56" height="52"/>
          <path d="M44 80 L58 64 L68 74 L74 68 L80 80"/>
          <path d="M30 112 H160"/>
          <rect x="44" y="112" width="30" height="42"/>
          <path d="M44 126 H74 M44 140 H74"/>
          <path d="M118 92 V118 H142 M128 118 V146 M114 150 H142"/>
          <path d="M150 112 L138 78 L124 66"/>
          <path d="M118 60 L134 54 L130 72 Z"/>
        </g>
      </svg>
      <p class="service-label">Private<br>Offices</p>
    </div>

    <div class="divider divider--one"></div>

    <div class="service service--virtual">
      <svg class="service-icon" viewBox="0 0 192 192" aria-hidden="true">
        <circle cx="96" cy="96" r="96" fill="var(--navy)"/>
        <g fill="none" stroke="var(--white)" stroke-width="4" stroke-linejoin="round" stroke-linecap="round">
          <path d="M60 82 H170 V150 H60 Z"/>
          <rect x="84" y="98" width="44" height="32"/>
          <path d="M84 98 L106 116 L128 98"/>
          <path d="M146 130 L156 120"/>
          <path d="M26 110 H50 L46 150 H30 Z"/>
          <path d="M38 110 C34 96 30 88 28 76 M38 110 C40 94 44 84 50 74"/>
        </g>
      </svg>
      <p class="service-label">Virtual<br>Offices</p>
    </div>

    <div class="divider divider--two"></div>

    <div class="service service--lounge">
      <svg class="service-icon" viewBox="0 0 192 192" aria-hidden="true">
        <circle cx="96" cy="96" r="96" fill="var(--navy)"/>
        <g fill="none" stroke="var(--white)" stroke-width="4" stroke-linejoin="round" stroke-linecap="round">
          <rect x="76" y="28" width="40" height="22" rx="4"/>
          <path d="M86 39 H106"/>
          <rect x="82" y="72" width="40" height="22" rx="4"/>
          <path d="M92 83 H112"/>
          <path d="M40 112 H152"/>
          <path d="M56 112 V158 M136 112 V158"/>
          <path d="M30 100 V158 M162 100 V158"/>
        </g>
        <g fill="var(--white)">
          <circle cx="84" cy="60" r="4"/>
          <circle cx="96" cy="60" r="4"/>
          <circle cx="108" cy="60" r="4"/>
        </g>
      </svg>
      <p class="service-label">Coworking<br>Lounge</p>
    </div>

    <p class="brand-name">2417 HARBORVIEW</p>
  </section>
</main>
</body>
</html>
```